Website Design for a Project Management Consulting Business

I have a logo design already and now I need a website.
I am a project manager and run my own consulting business.
Currently I am under contract with 3 major Vantage 400 companies. I'd like a website I can direct current and future clients.
My job is running IT projects and working with developers to deliver business priorities.
The website should be professional and clean - I work IT projects and would like to incorporate that into any theme.
I'd like the site to have several page or breakoff links - sections would include : about me, about my services, a page to display all of my certification badges, another page to talk about highlights from past projects and so on.
Looking for a collaborative experience.

Industry/Entity Type

Vantage 400 Consulting Firm - Project Management

Coding

Coded - Design and coding required

Number of Pages Required

1 page

Font styles to use
Serif

Colors
0094D4
00A9DD
6FCCEA
C7EBF8
E9F6FB
EE7325
F08F49
F5BC92
FAE3D3
FDF4ED

Requirements
Must have
• Sections that are a must: About Me (bio), About My Services, About my Certifications and Credentials, Experience on Past Projects,
Nice to have
• I have added the logo below - I'd like to use the logo and have it prominent ; should be professional and inviting

```html
<!DOCTYPE html>
<html lang="en">
<head>
<meta charset="utf-8">
<title>Keystone Project Management LLC</title>
<link rel="stylesheet" href="https://fonts.googleapis.com/css2?family=Barlow+Condensed:wght@500;600;700&family=Barlow:wght@400;500;600&family=Inter:wght@400;500;600&display=swap">
<style>
:root{
  --navy:#13325f;
  --orange:#ee7325;
  --blue:#0a8fd6;
  --sky:#6fcce6;
  --band:#f2f2f2;
  --line:#c7ebf8;
  --text:#2f3440;
  --white:#ffffff;
}
*{margin:0;padding:0;box-sizing:border-box}
html,body{width:1200px;height:3745px;overflow:hidden}
body{position:relative;background:var(--white);font-family:"Inter",sans-serif;color:var(--text)}
.abs{position:absolute}
.band{position:absolute;left:0;width:1200px;background:var(--band)}
.cond{font-family:"Barlow Condensed",sans-serif}
.heading{position:absolute;font-family:"Barlow Condensed",sans-serif;font-weight:700;color:var(--navy);text-transform:uppercase;letter-spacing:.2px;line-height:1}
.heading em{font-style:normal;color:var(--orange)}
.bracket{position:absolute;border-top:5px solid var(--blue);border-right:5px solid var(--blue)}
.photo{position:absolute}
.btn{position:absolute;display:flex;align-items:center;justify-content:center;background:var(--blue);color:var(--white);border-radius:21px;font-family:"Barlow Condensed",sans-serif;font-weight:700;font-size:17px;letter-spacing:1px;text-transform:uppercase}
.body-text{position:absolute;font-size:15.5px;line-height:24px;color:var(--text)}

/* header */
.brand{position:absolute;left:157px;top:20px;display:flex;align-items:center;gap:12px}
.brand-mark{width:42px;height:42px;border:4px solid var(--navy)}
.brand-name{font-family:"Barlow",sans-serif;font-weight:600;color:var(--navy);font-size:30px;letter-spacing:1px;line-height:1}
.brand-sub{font-family:"Barlow",sans-serif;font-weight:600;color:var(--navy);font-size:10px;letter-spacing:3.4px;display:block}
.contact-top{position:absolute;top:22px;font-family:"Barlow Condensed",sans-serif;font-size:17px;color:var(--navy)}
.contact-top b{display:block;color:var(--blue);font-weight:600;font-size:17px;margin-top:2px}
.contact-top svg{position:absolute;left:-27px;top:2px}
.topline{position:absolute;left:0;top:90px;width:1200px;height:2px;background:var(--line)}
.nav{position:absolute;left:157px;top:112px;display:flex;gap:31px;font-family:"Barlow",sans-serif;font-size:14.5px;letter-spacing:1.3px;color:var(--navy)}
.nav span::before{content:"";display:inline-block;width:18px;height:1.5px;background:var(--navy);vertical-align:middle;margin-right:12px}

/* services */
.service{position:absolute;display:flex;gap:20px;align-items:flex-start}
.service i{display:block;width:38px;height:38px;border:3.5px solid var(--navy);flex:none;margin-top:2px}
.service span{font-family:"Barlow",sans-serif;font-weight:600;color:var(--navy);font-size:18px;line-height:26px;letter-spacing:.3px;text-transform:uppercase}

/* stats */
.stat{position:absolute}
.stat b{display:block;font-family:"Barlow Condensed",sans-serif;font-weight:700;color:var(--orange);font-size:33px;line-height:1}
.stat span{font-family:"Barlow Condensed",sans-serif;font-weight:600;color:var(--navy);font-size:17px}

/* certs */
.cert{position:absolute;top:1763px;width:80px;height:80px}
.arrow-nav{position:absolute;top:1785px}

/* experience */
.exp-card{position:absolute;top:2633px;width:274px}
.exp-photo{margin:0 auto;width:208px;height:225px}
.exp-label{height:96px;background:var(--blue);color:var(--white);display:flex;align-items:center;justify-content:center;text-align:center;font-family:"Barlow Condensed",sans-serif;font-weight:700;font-size:24px;line-height:27px;letter-spacing:.4px}

/* contact */
.divider-h{position:absolute;left:0;top:3047px;width:1200px;height:2px;background:var(--line)}
.divider-v{position:absolute;left:537px;top:3047px;width:2px;height:450px;background:var(--line)}
.info-row{position:absolute;left:157px;display:flex;align-items:flex-start;gap:13px;font-family:"Barlow Condensed",sans-serif;font-size:19px;color:var(--navy)}
.info-row .dot{width:29px;height:29px;border-radius:50%;background:var(--blue);display:flex;align-items:center;justify-content:center;flex:none}
.info-row b{font-weight:600;color:var(--navy)}
.info-row u{font-weight:600}
.field{position:absolute;height:36px;border:1.5px solid var(--navy);border-radius:6px;padding:10px 16px;font-family:"Barlow Condensed",sans-serif;font-size:13.5px;letter-spacing:.5px;color:var(--navy)}

/* footer */
.footer{position:absolute;left:0;top:3497px;width:1200px;height:248px;background:var(--band)}
.footer-card{position:absolute;left:681px;top:3497px;width:360px;height:248px;background:var(--white)}
.foot-h{position:absolute;top:3560px;font-family:"Barlow Condensed",sans-serif;font-weight:700;font-size:19px;color:var(--navy)}
.foot-links{position:absolute;top:3600px;font-family:"Inter",sans-serif;font-size:11.5px;line-height:24px;color:var(--navy)}
.social{position:absolute;left:0;width:360px;top:3648px;display:flex;justify-content:center;gap:17px}
.social i{display:block;width:15px;height:15px;border-radius:50%;background:var(--blue)}
.copyright{position:absolute;left:0;top:3687px;width:360px;text-align:center;font-size:11.5px;color:var(--navy)}
</style>
</head>
<body>

<!-- header -->
<div class="brand">
  <div class="brand-mark"></div>
  <div><span class="brand-sub">PROJECT MANAGEMENT</span><span class="brand-name">KEYSTONE</span><span class="brand-sub" style="text-align:center">LLC</span></div>
</div>
<div class="contact-top" style="left:681px">
  <svg width="17" height="17" viewBox="0 0 24 24"><path d="M6.6 10.8a15.5 15.5 0 0 0 6.6 6.6l2.2-2.2c.3-.3.7-.4 1-.2 1.1.4 2.3.6 3.6.6.6 0 1 .4 1 1V20c0 .6-.4 1-1 1A17 17 0 0 1 3 4c0-.6.4-1 1-1h3.5c.6 0 1 .4 1 1 0 1.3.2 2.5.6 3.6.1.3 0 .7-.2 1z" fill="none" stroke="#ee7325" stroke-width="2"/></svg>
  Call Me<b>(555) 010-2847</b>
</div>
<div class="contact-top" style="left:850px">
  <svg width="17" height="17" viewBox="0 0 24 24"><rect x="3" y="5" width="18" height="14" rx="1" fill="none" stroke="#ee7325" stroke-width="2"/><path d="M3 6l9 7 9-7" fill="none" stroke="#ee7325" stroke-width="2"/></svg>
  Emai Me<b>hello@keystonepm.example</b>
</div>
<div class="topline"></div>
<nav class="nav"><span>ABOUT ME</span><span>MY SERVICES</span><span>CERTIFICATIONS AND CREDENTIALS</span><span>EXPERIENCE</span><span>CONTACT</span></nav>

<!-- hero -->
<div class="band" style="top:199px;height:326px"></div>
<div class="photo" role="img" aria-label="Portrait photo of the consultant in a pinstripe suit" style="left:157px;top:154px;width:418px;height:418px;background:linear-gradient(160deg,#1a1a1a 0%,#3b2a22 45%,#111 100%)"></div>
<div class="bracket" style="left:948px;top:199px;width:93px;height:92px"></div>
<div class="heading" style="left:623px;top:246px;font-size:40px">Extensive Experienced</div>
<div class="heading" style="left:623px;top:292px;font-size:52px"><em>Consultant</em></div>
<div class="body-text" style="left:624px;top:355px;width:380px;font-size:17px;line-height:26px">Serves as Principal Lead Consultant on waterfall and agile contract opportunities.</div>
<div class="btn" style="left:624px;top:433px;width:183px;height:41px">My Experience</div>

<!-- services -->
<div class="bracket" style="left:972px;top:618px;width:69px;height:70px"></div>
<div class="heading" style="left:560px;top:640px;width:455px;text-align:right;font-size:48px">About <em>My Services</em></div>
<div class="service" style="left:157px;top:738px"><i></i><span>Leading Lean Agile<br>Scrum Teams</span></div>
<div class="service" style="left:470px;top:738px"><i></i><span>Leading Lean Agile<br>Scrum Teams</span></div>
<div class="service" style="left:761px;top:738px"><i></i><span>Leading Lean Agile<br>Scrum Teams</span></div>
<div class="service" style="left:157px;top:828px"><i></i><span>Leading Lean Agile<br>Scrum Teams</span></div>
<div class="service" style="left:470px;top:828px"><i></i><span>Leading Lean Agile<br>Scrum Teams</span></div>
<div class="service" style="left:761px;top:828px"><i></i><span>Leading Lean Agile<br>Scrum Teams</span></div>

<!-- about me -->
<div class="band" style="top:1015px;height:488px"></div>
<div class="photo" role="img" aria-label="Full-length photo of the consultant in a blue plaid suit" style="left:625px;top:977px;width:416px;height:576px;background:linear-gradient(180deg,#f4f4f4 0%,#9fb4cc 45%,#5d7ea6 100%)"></div>
<div class="bracket" style="left:291px;top:1089px;width:70px;height:70px"></div>
<div class="heading" style="left:158px;top:1112px;font-size:48px">About <em>Me</em></div>
<div class="body-text" style="left:158px;top:1188px;width:420px;font-size:14.5px">Marcus Ellison is the Owner of Keystone Project Management, LLC and serves as Principal Lead Consultant on waterfall and agile contract opportunities.</div>
<div class="stat" style="left:158px;top:1290px"><b>500+</b><span>Satisfied Clients</span></div>
<div class="stat" style="left:330px;top:1290px"><b>99%</b><span>Success of Works</span></div>
<div class="btn" style="left:158px;top:1389px;width:235px;height:41px">Know More About Me</div>

<!-- certifications -->
<div class="bracket" style="left:687px;top:1633px;width:69px;height:70px"></div>
<div class="heading" style="left:157px;top:1658px;font-size:48px">Certifications <em>&amp; Credentials</em></div>
<svg class="arrow-nav" style="left:159px" width="20" height="36" viewBox="0 0 20 36"><path d="M18 2L3 18l15 16" fill="none" stroke="#c7ccd6" stroke-width="2"/></svg>
<svg class="arrow-nav" style="left:1020px" width="20" height="36" viewBox="0 0 20 36"><path d="M2 2l15 16L2 34" fill="none" stroke="#c7ccd6" stroke-width="2"/></svg>
<svg class="cert" style="left:210px" viewBox="0 0 80 80"><circle cx="40" cy="40" r="36" fill="#fff" stroke="#5a2d8c" stroke-width="5"/></svg>
<svg class="cert" style="left:348px" viewBox="0 0 80 80"><circle cx="40" cy="40" r="36" fill="#fff" stroke="#5a2d8c" stroke-width="5"/></svg>
<svg class="cert" style="left:485px" viewBox="0 0 80 80"><path d="M40 2L78 40 40 78 2 40z" fill="#1d3a63" stroke="#9fb3c8" stroke-width="2"/></svg>
<svg class="cert" style="left:623px" viewBox="0 0 80 80"><path d="M40 2L78 40 40 78 2 40z" fill="#1d3a63" stroke="#9fb3c8" stroke-width="2"/></svg>
<svg class="cert" style="left:761px" viewBox="0 0 80 80"><circle cx="40" cy="40" r="37" fill="#e8552e"/></svg>
<svg class="cert" style="left:900px" viewBox="0 0 80 80"><circle cx="40" cy="40" r="37" fill="#f2a51e"/></svg>

<!-- testimonial -->
<div class="band" style="top:2004px;height:415px"></div>
<div class="photo" role="img" aria-label="Close-up photo of the consultant at an office desk" style="left:157px;top:1956px;width:416px;height:508px;background:linear-gradient(160deg,#c9c4bd 0%,#6a5548 45%,#2c2f3a 100%)"></div>
<div class="bracket" style="left:960px;top:2045px;width:67px;height:70px"></div>
<div class="heading" style="left:633px;top:2071px;font-size:46px">Trusted By Biggest</div>
<div class="heading" style="left:633px;top:2125px;font-size:46px"><em>Business Names</em></div>
<div class="body-text" style="left:633px;top:2196px;width:400px;font-size:15px">Lorem ipsum dolor sit amet, consectetur adipiscing elit, sed do eiusmod tempor incididunt ut labore et dolore magna aliqua. Ut enim ad minim veniam, quis nostrud exercitation ullamco laboris nisi ut aliquip ex ea commodo consequat.</div>
<div class="abs" style="left:633px;top:2330px;font-weight:600;font-size:14.5px;color:var(--navy)">DANIEL REEVES</div>
<div class="abs" style="left:633px;top:2354px;font-size:14.5px">Brightline Startup</div>
<div class="abs cond" style="left:972px;top:2296px;font-size:120px;line-height:1;font-weight:700;color:var(--sky)">&rdquo;</div>

<!-- experience -->
<div class="bracket" style="left:972px;top:2502px;width:69px;height:70px"></div>
<div class="heading" style="left:700px;top:2525px;width:311px;text-align:right;font-size:48px"><em>Experience</em></div>
<div class="exp-card" style="left:157px">
  <div class="exp-photo" role="img" aria-label="Photo of the consultant in a tan jacket" style="background:linear-gradient(180deg,#5a4636 0%,#8c6a4e 60%,#2d2420 100%)"></div>
  <div class="exp-label">SENIOR LEAD SCRUM<br>MASTER</div>
</div>
<div class="exp-card" style="left:463px">
  <div class="exp-photo" role="img" aria-label="Photo of the consultant in a blue plaid suit" style="background:linear-gradient(180deg,#eef0f3 0%,#9fb4cc 55%,#5d7ea6 100%)"></div>
  <div class="exp-label">SENIOR LEAD SCRUM<br>MASTER</div>
</div>
<div class="exp-card" style="left:768px">
  <div class="exp-photo" role="img" aria-label="Photo of the consultant in a pinstripe suit" style="background:linear-gradient(180deg,#111 0%,#3b2a22 50%,#2b2e3a 100%)"></div>
  <div class="exp-label">SENIOR LEAD SCRUM<br>MASTER</div>
</div>

<!-- contact -->
<div class="divider-h"></div>
<div class="divider-v"></div>
<div class="bracket" style="left:350px;top:3110px;width:70px;height:70px"></div>
<div class="heading" style="left:157px;top:3130px;font-size:48px">Get <em>In Touch</em></div>
<div class="body-text" style="left:158px;top:3200px;width:340px;font-size:14.5px">We’re glad to discuss your organisation’s situation. So please contact us via the details below, or enter your request.</div>
<div class="info-row" style="top:3300px">
  <span class="dot"><svg width="14" height="16" viewBox="0 0 14 18"><path d="M7 1a6 6 0 0 0-6 6c0 4.5 6 10 6 10s6-5.5 6-10a6 6 0 0 0-6-6z" fill="#fff"/><circle cx="7" cy="7" r="2.2" fill="#0a8fd6"/></svg></span>
  <span>Address - &nbsp;</span><span style="line-height:26px">48 Cedar Lane, Albany,<br>NY, 12207, USA,</span>
</div>
<div class="info-row" style="top:3362px">
  <span class="dot"><svg width="14" height="14" viewBox="0 0 24 24"><path d="M6.6 10.8a15.5 15.5 0 0 0 6.6 6.6l2.2-2.2c.3-.3.7-.4 1-.2 1.1.4 2.3.6 3.6.6.6 0 1 .4 1 1V20c0 .6-.4 1-1 1A17 17 0 0 1 3 4c0-.6.4-1 1-1h3.5c.6 0 1 .4 1 1 0 1.3.2 2.5.6 3.6.1.3 0 .7-.2 1z" fill="#fff"/></svg></span>
  <span>Call Me - &nbsp;</span><b>(555) 010-2847</b>
</div>
<div class="info-row" style="top:3400px">
  <span class="dot"><svg width="14" height="12" viewBox="0 0 24 20"><rect x="2" y="2" width="20" height="16" rx="1" fill="none" stroke="#fff" stroke-width="2.4"/><path d="M2 3l10 8 10-8" fill="none" stroke="#fff" stroke-width="2.4"/></svg></span>
  <span>Emai Me - &nbsp;</span><u>hello@keystonepm.example</u>
</div>
<div class="field" style="left:579px;top:3119px;width:222px">FIRST NAME</div>
<div class="field" style="left:819px;top:3119px;width:222px">LAST NAME</div>
<div class="field" style="left:579px;top:3175px;width:222px">EMAIL ADDRESS</div>
<div class="field" style="left:819px;top:3175px;width:222px">PHONE</div>
<div class="field" style="left:579px;top:3230px;width:222px">WEBSITE</div>
<div class="field" style="left:819px;top:3230px;width:222px">SERVICES</div>
<div class="field" style="left:579px;top:3284px;width:460px;height:102px">MESSAGE</div>
<div class="btn" style="left:857px;top:3407px;width:182px;height:41px">Send Request</div>

<!-- footer -->
<div class="footer"></div>
<div class="foot-h" style="left:157px">USEFULL LINKS</div>
<div class="foot-h" style="left:481px">SERVICES</div>
<div class="foot-links" style="left:157px;width:140px">- About Me<br>- Experience<br>- Certifications and<br>&nbsp;&nbsp;Credentials<br>- Contact Us</div>
<div class="foot-links" style="left:310px">- Privacy Policy<br>- Terms &amp; Conditions</div>
<div class="foot-links" style="left:481px">- Services1<br>- Services1<br>- Services1<br>- Services1</div>
<div class="footer-card">
  <div class="brand" style="left:30px;top:62px">
    <div class="brand-mark"></div>
    <div><span class="brand-sub">PROJECT MANAGEMENT</span><span class="brand-name">KEYSTONE</span><span class="brand-sub" style="text-align:center">LLC</span></div>
  </div>
</div>
<div class="social" style="left:681px"><i></i><i></i><i></i><i></i></div>
<div class="copyright" style="left:681px">Copyright © 2022 KEYSTONE LLC. All rights reserved.</div>

</body>
</html>
```